Velvet Pressings Techno Label Business Card

I'm looking for a very clean business card for my Velvet Pressings music label. The label focusses on techno music. The card should include:

• my name : Tomas Brandt as "Founder & CEO"
• email address: tomas@velvet-pressings.example
• web: www.velvet-pressings.example
• facebook logo + /velvetpress
• twitter logo + /velvetpress
• soundcloud logo + /velvetpressings

Feel free to include your ideas! I'm looking forward to discuss about it.

Tomas

Industry/Entity Type

Business

Contact Information for Business Card

I don't like glossy cards. Prefer matt.

Requirements
Nice to have
• Maybe on one side the complete logo, other side just the icon.
Should not have
• Flashy stuff. Must be clean and business like style.

```html
<!DOCTYPE html>
<html lang="en">
<head>
<meta charset="utf-8">
<title>Velvet Pressings — Business Card</title>
<link href="https://fonts.googleapis.com/css2?family=Signika:wght@600&family=Maven+Pro:wght@400&family=Open+Sans:wght@400&family=Arimo:wght@400&display=swap" rel="stylesheet">
<style>
  :root {
    --page: #f7f7f7;
    --card: #0b0c0e;
    --orange: #e8701a;
    --grey: #6f6f6f;
    --muted: #9a9a9a;
    --spec-title: #d8264f;
    --spec-text: #222222;
  }
  * { margin: 0; padding: 0; box-sizing: border-box; }
  html, body { width: 1200px; height: 1066px; overflow: hidden; }
  body { background: var(--page); position: relative; }

  .card {
    position: absolute;
    width: 651px;
    height: 393px;
    background: var(--card);
    box-shadow: -18px 22px 40px rgba(0, 0, 0, 0.18);
  }
  .card--front { left: 125px; top: 111px; }
  .card--back  { left: 388px; top: 561px; }

  .brand {
    position: absolute;
    left: 150px;
    top: 166px;
    display: flex;
    align-items: center;
    gap: 16px;
  }
  .brand__square {
    width: 14px; height: 14px;
    background: var(--grey);
    flex: none;
  }
  .brand__name {
    font-family: "Signika", sans-serif;
    font-weight: 600;
    font-size: 44px;
    line-height: 1;
    color: var(--orange);
  }

  .person { position: absolute; left: 327px; top: 70px; }
  .person__name {
    font-family: "Maven Pro", sans-serif;
    font-size: 22px;
    color: var(--orange);
    letter-spacing: 0.6px;
    line-height: 1.2;
  }
  .person__role {
    font-family: "Maven Pro", sans-serif;
    font-size: 13px;
    color: var(--muted);
    letter-spacing: 0.5px;
    margin-top: 2px;
  }

  .contacts {
    position: absolute;
    left: 333px; top: 208px;
    list-style: none;
  }
  .contacts__item {
    display: flex;
    align-items: center;
    height: 22.4px;
    font-family: "Open Sans", sans-serif;
    font-size: 15.5px;
    color: var(--muted);
  }
  .contacts__icon { width: 11px; height: 11px; margin-right: 10px; flex: none; }
  .contacts__square { width: 10px; height: 10px; border-radius: 2px; background: var(--orange); margin-right: 11px; flex: none; }

  .spec {
    position: absolute;
    left: 888px; top: 157px;
    font-family: "Arimo", sans-serif;
  }
  .spec__title { font-size: 26px; color: var(--spec-title); margin-bottom: 46px; }
  .spec__values { list-style: none; font-size: 27px; color: var(--spec-text); line-height: 30.5px; }
</style>
</head>
<body>

  <section class="card card--front" aria-label="Card front">
    <div class="brand">
      <span class="brand__square" aria-hidden="true"></span>
      <span class="brand__name">Velvet Pressings</span>
    </div>
  </section>

  <section class="card card--back" aria-label="Card back">
    <div class="person">
      <p class="person__name">Tomas Brandt</p>
      <p class="person__role">Founder &amp; CEO</p>
    </div>

    <ul class="contacts">
      <li class="contacts__item">
        <svg class="contacts__icon" viewBox="0 0 12 12" aria-hidden="true">
          <rect x="0.5" y="2.5" width="11" height="7.5" fill="var(--orange)"/>
          <path d="M0.5 2.5 L6 6.8 L11.5 2.5" fill="none" stroke="var(--card)" stroke-width="1.2"/>
        </svg>
        tomas@velvet-pressings.example
      </li>
      <li class="contacts__item">
        <svg class="contacts__icon" viewBox="0 0 12 12" aria-hidden="true">
          <circle cx="6" cy="6" r="5.2" fill="var(--orange)"/>
          <path d="M0.8 6 H11.2 M6 0.8 V11.2 M6 0.8 C3 3.5 3 8.5 6 11.2 M6 0.8 C9 3.5 9 8.5 6 11.2" fill="none" stroke="var(--card)" stroke-width="0.8"/>
        </svg>
        www.velvet-pressings.example
      </li>
      <li class="contacts__item"><span class="contacts__square" aria-hidden="true"></span>/velvetpress</li>
      <li class="contacts__item"><span class="contacts__square" aria-hidden="true"></span>/velvetpress</li>
      <li class="contacts__item"><span class="contacts__square" aria-hidden="true"></span>/velvetpressings</li>
    </ul>
  </section>

  <aside class="spec">
    <p class="spec__title">Black</p>
    <ul class="spec__values">
      <li>C:100</li>
      <li>M:100</li>
      <li>Y:100</li>
      <li>K:100</li>
    </ul>
  </aside>

</body>
</html>
```